strength and conditioning business focused on helping people move more efficiently

I need a business card designed for a Philadelphia based company called Brsk Lft Motion (pronounced Brisk Lift). We offer fitness professional services with the idea of helping people feel better and move optimally. We do this by designing and walking through individualized programs as well as minor soft tissue work. Our perfect client would be athletes but we will be marketing to parents who have children that are active They remember their former athletic days and want to get as close as possible back to that feeling. Attached will be the official logo and logo formats. I would love for the design to communicate trustworthy and creative. I would also love for the design to be square with rounded edges.

Target Market(s)

Parents of athletic children
former athletes
athletes

Industry/Entity Type

Fitness

Contact Information for Business Card

Business: Brsk Lft Performance
Name: Coach Calvin Ashworth
Position: Strength and Conditioning Coach / Certified Personal Trainer
Contact: coach.ash@brsklft.com
Text: (555)204-7781

Font styles to use
Serif
Sans Serif

Colors
fbee38
fbee3e
0255a3
3176b5
ffffff

Requirements
Must have
• use of logo
Nice to have
• Square design
rounded edges

```html
<!DOCTYPE html>
<html lang="en">
<head>
<meta charset="UTF-8">
<title>Brsk Lft Motion – Business Card</title>
<link rel="stylesheet" href="https://fonts.googleapis.com/css2?family=Arimo:wght@400;700&display=swap">
<style>
  :root {
    --navy: #0b2f80;
    --yellow: #f9c80e;
    --white: #ffffff;
    --ink: #2b2b2b;
    --backdrop: #2a2a2a;
  }
  * { margin: 0; padding: 0; box-sizing: border-box; }
  html, body {
    width: 1200px; height: 859px; overflow: hidden;
    background: var(--backdrop);
    font-family: "Arimo", Arial, sans-serif;
  }
  .canvas { position: relative; width: 1200px; height: 859px; }

  .card {
    position: absolute; top: 208px;
    width: 446px; height: 446px;
    border-radius: 30px; overflow: hidden;
  }
  .card--front { left: 142px; background: var(--white); }
  .card--back  { left: 626px; background: var(--navy); }

  .brand {
    position: absolute; left: 0; right: 0;
    display: flex; align-items: center; justify-content: center; gap: 12px;
    font-weight: 700; letter-spacing: 0.5px;
  }
  .brand__dot { width: 34px; height: 34px; border-radius: 50%; background: var(--yellow); flex: none; }
  .card--front .brand { top: 88px; font-size: 40px; color: var(--navy); }
  .card--back  .brand { top: 200px; font-size: 40px; color: var(--white); }

  .person {
    position: absolute; top: 210px; left: 0; right: 0;
    text-align: center; font-size: 20px; font-weight: 700;
  }
  .person__first { color: var(--yellow); }
  .person__last { color: var(--navy); }
  .role {
    position: absolute; top: 238px; left: 0; right: 0;
    text-align: center; font-size: 15.5px; line-height: 20px; color: var(--ink);
  }

  .divider {
    position: absolute; top: 290px; left: 0; right: 0;
    display: flex; align-items: center; justify-content: center; gap: 4px;
  }
  .divider__rule { width: 44px; height: 1.5px; background: var(--yellow); margin: 0 8px; }
  .divider__icon {
    width: 25px; height: 25px; border-radius: 50%; background: var(--navy);
    display: flex; align-items: center; justify-content: center;
  }

  .contacts {
    position: absolute; top: 328px; left: 0; right: 0;
    text-align: center; font-size: 16.5px; line-height: 21.5px; color: var(--ink);
    list-style: none;
  }

  .footer-band { position: absolute; left: 0; bottom: 0; width: 446px; height: 12px; }
</style>
</head>
<body>
<div class="canvas">

  <section class="card card--front">
    <div class="brand"><span class="brand__dot"></span><span class="brand__name">Brsk Lft Motion</span></div>

    <p class="person"><span class="person__first">Coach Calvin</span> <span class="person__last">Ashworth</span></p>
    <p class="role">Strength and Conditioning Coach /<br>Certified Personal Trainer</p>

    <div class="divider">
      <span class="divider__rule"></span>
      <span class="divider__icon">
        <svg width="13" height="13" viewBox="0 0 24 24"><path fill="#fff" d="M6.6 10.8a15.1 15.1 0 0 0 6.6 6.6l2.2-2.2a1 1 0 0 1 1-.25 11.4 11.4 0 0 0 3.6.57 1 1 0 0 1 1 1V20a1 1 0 0 1-1 1A17 17 0 0 1 3 4a1 1 0 0 1 1-1h3.5a1 1 0 0 1 1 1c0 1.25.2 2.45.57 3.6a1 1 0 0 1-.25 1z"/></svg>
      </span>
      <span class="divider__icon">
        <svg width="13" height="13" viewBox="0 0 24 24"><rect x="2" y="5" width="20" height="14" rx="1.5" fill="#fff"/><path d="M2.5 6l9.5 7 9.5-7" stroke="#0b2f80" stroke-width="2" fill="none"/></svg>
      </span>
      <span class="divider__icon">
        <svg width="13" height="13" viewBox="0 0 24 24"><circle cx="12" cy="12" r="9.5" fill="none" stroke="#fff" stroke-width="2"/><ellipse cx="12" cy="12" rx="4" ry="9.5" fill="none" stroke="#fff" stroke-width="1.8"/><path d="M2.5 12h19" stroke="#fff" stroke-width="1.8"/></svg>
      </span>
      <span class="divider__rule"></span>
    </div>

    <ul class="contacts">
      <li>(555)204-7781</li>
      <li>coach.ash@brsklft.com</li>
      <li>www.brsklft.com</li>
    </ul>

    <svg class="footer-band" viewBox="0 0 446 12" preserveAspectRatio="none">
      <polygon points="0,0 224,0 214,12 0,12" fill="var(--navy)"/>
      <polygon points="230,0 446,0 446,12 220,12" fill="var(--yellow)"/>
    </svg>
  </section>

  <section class="card card--back">
    <div class="brand"><span class="brand__dot"></span><span class="brand__name">Brsk Lft Motion</span></div>
  </section>

</div>
</body>
</html>
```